dsadasdasdasdsa

Industry/Entity Type

Mortgage Broking

Requirements
Must have
• Call-to-action button somewhere on the graphic
Nice to have
• The font of our logo is Montserrat

```html
<!DOCTYPE html>
<html lang="en">
<head>
<meta charset="UTF-8">
<title>Mortgage Broker Directory Banner</title>
<link rel="stylesheet" href="https://fonts.googleapis.com/css2?family=Montserrat:wght@500;600;800;900&display=swap">
<style>
  :root {
    --bg-deep: #0f5a32;
    --bg-mid: #1d9a59;
    --panel-top: #ffffff;
    --panel-bottom: #b8ecc8;
    --headline: #1d5a34;
    --kicker: #b8322a;
    --cta: #b8322a;
    --cta-text: #ffffff;
    --mascot-light: #6cc06a;
    --mascot-dark: #8a5a2e;
  }
  * { margin: 0; padding: 0; box-sizing: border-box; }
  html, body {
    width: 1200px;
    height: 180px;
    overflow: hidden;
  }
  body {
    font-family: "Montserrat", sans-serif;
  }
  .banner {
    position: relative;
    width: 1200px;
    height: 180px;
    background: radial-gradient(ellipse 60% 120% at 55% 50%, var(--bg-mid) 0%, var(--bg-deep) 75%);
    overflow: hidden;
  }
  .panel {
    position: absolute;
    left: 32px;
    top: 22px;
    width: 1133px;
    height: 132px;
    border-radius: 22px;
    background: linear-gradient(180deg, var(--panel-top) 35%, var(--panel-bottom) 100%);
  }
  .copy {
    position: absolute;
    left: 64px;
    top: 34px;
  }
  .kicker {
    color: var(--kicker);
    font-weight: 500;
    font-size: 28px;
    line-height: 32px;
    letter-spacing: 0.2px;
  }
  .headline {
    margin-top: 4px;
    color: var(--headline);
    font-weight: 900;
    font-size: 33px;
    line-height: 34px;
    text-transform: uppercase;
    letter-spacing: 0.3px;
  }
  .mascot {
    position: absolute;
    left: 735px;
    top: 0;
    width: 245px;
    height: 180px;
    border-radius: 110px 110px 40px 40px;
    background: radial-gradient(ellipse at 40% 30%, var(--mascot-light) 0%, #3f9a4e 45%, var(--mascot-dark) 100%);
  }
  .cta {
    position: absolute;
    left: 984px;
    top: 71px;
    width: 161px;
    height: 39px;
    border-radius: 20px;
    background: var(--cta);
    color: var(--cta-text);
    font-weight: 800;
    font-size: 17px;
    line-height: 39px;
    text-align: center;
    text-decoration: none;
    letter-spacing: 0.2px;
  }
</style>
</head>
<body>
  <div class="banner">
    <div class="panel"></div>
    <div class="copy">
      <p class="kicker">Need a Mortgage Broker?</p>
      <h1 class="headline">Search now on Australia’s<br>largest directory</h1>
    </div>
    <div class="mascot" role="img" aria-label="Friendly cartoon turtle mascot holding a small house"></div>
    <a class="cta" href="#">CLICK HERE</a>
  </div>
</body>
</html>
```